Velmora Gems - High end custom Jewelry website

I need a web design for an online custom jewelry company called Velmora Gems. (www.velmoragems-demo.com) this company specializes in high-end custom made engagement rings, wedding bands and jewelry of all kinds (necklaces, earrings, bracelets etc)All our jewelry uses diamonds so there must be a focus on diamonds on every type of jewelry we will be designing off the website.

We are a company located in New York City but our website will
aim to cater to international, national clients and as well as New York city residents.The company low overhead provides diamonds and precious metal at a discounted costs compared to its competitors. Velmora Gems makes unique custom diamond jewelry of a higher quality and at a lower price than carriage trade retail jewellers. (meaning that our company allows our customers to save money on diamond jewelry then they would if they bought from any known store or company)

The website will act as a tool for our customers to create their own jewelry. The way they will do this is by uploading pictures of what they like, they can post any pictures they want (from drawings, to actual copy and pasted pictures from other websites of designs) From these designs we will create a 3D digital image of the jewelry they like and customize it - however they want (colours, size etc) and then give them a quote in price. From the quote they will either approve it and we can have it made for them in 1 weeks time. If they decline it we will try to do whatever it is they want for the design to suit their needs.

We want the website to be simple and user friendly since people will be working on it to create their own individual jewelry pieces. Therefore some useful headings should include:

"Custom Jewellery" or something like "your design" "Custom Design"

a drop heading here should show the following steps into creating the jewelry.

step 1:
upload pictures of the designs you like
step 2:
What is your ring size?
Step 3:
What setting would you like your ring in? platinum, 14k etc..
Step 4:
What is your budget?
Step 5 :
Once you’ve uploaded pictures and give an explanation of what you want then we will contact you by phone or email and proceed to design your ring. Give us your contact info in this step.

Other then that other headings id like to see on the site are:

"Home"
main page with appealing picture which I can later add text to it explaining our company

"About us"
will include a brief section of who we are

"Wedding/engagment"

We are based in New York City and our company offers a one-to-one personal service to our clients ensuring their expectations are well met and, if we can help it, surpassed. We are a personal shopping and diamond supplier to individuals. Custom design is our speciality weather it be wedding ring, engagement ring or anniversary ring we aim to create distinctive designs that both reflect your personality as well as the beauty of the gemstones used in your piece. We use platinum, 14l-18k gold and diamonds to whatever it is that you may desire.
We in our company believe that we are privileged to be a part of one of the biggest events in our customer’s lives, and we pride ourselves on making sure that our customers have the best experience possible. As the diamond is the center piece of every engagement ring, we at VG make sure that our clients find the best diamond possible that is within their budget. Similarly, we work with established jewellery artisans from Belgium to provide the highest possible craftsmanship to a ring design of your choice. We make sure that our rings are made by the true and tried traditional methods focused on quality rather than quantity and of course our diamonds are QRB certified.

Diamonds

A section that explains where our diamonds come from. A heading will drop down here that is a diamond guide, as shown below.
Diamond Guide

An overview of the 4 C’s and different settings, a section for a brief education on diamonds.
Client Experiences

A section where clients share their experiences with Velmora Gems and can post pictures and share stories about their engagement etc.

The colour i would like to see are white and black, white and dark blue or royal blue. I don't think pastel colours will look good with this, maybe accents of purple or something pastel but for the main colours I want to keep it classic and sophisticated since it is a diamond company.

"Sign in | Check out"
where users are able to create a profile and upload their pictures and create their designs..

and a "search section"

or something along these lines or if you can incorporate both:

Exquisite craftsmanship Finest quality diamonds
Will beat any competitors price by twenty to seventy percent guaranteed
Price quotes whitin24 hours

Upload design picture or sketch
Receive price quote within 24hours
Receive and approve free customized design
Receive you jewelry in 1 week or less

Engagment Ring or necklace, earring, etc
Name
EMail
phone
Competitior Link
Budget

The final design should communicate that Velmora Gems is a custom jewelry site that allows individuals to personalize any type of jewellery they want with diamonds - at a fraction of the cost in comparison to any other out there. Our team works very hard to ensure that you will be so involved in the custom order process that there is no chance of something not being made to your requests. Jewelry is made to the highest standard or it does not ship in the first place. In the event a custom order does not suit a customer, we will take returns within 14 days of delivery less a 25% restocking fee.

Target Market(s)

middle class and upper class people ages 25-45

Industry/Entity Type

Digital

Requirements
Must have
• We have the logo now that I will attach BUT if you want to design something else please feel free ! I am open to all designs and ideas.
My logo now is simply a sketch so even if we make it look a bit more professional and classy I would like that, I think I want to keep it simple just black and white and maybe make the diamond shiny if possible. other then black in white I liked the gold and black combination too.. but as I said open to any other creative ideas!

can take pictures of jewelry off this website:
http://www.plinthwaredesigns.example/library/rings.html
Nice to have
• We already have a logo but we would like to see a banner or something that indicated saving money on diamond jewelry without it looking tacky or too cheap..

Also would like to see artistic pictures if you can of jewelry alongside very simple designs of jewelry that the masses like, (anything trendy or appealing to the eye)

cursive or elegant writing could be nice, flash could also be incorporated in the main page..

Should not have
• Nothing to old fashioned, when I mean elegant maybe just the the name of the company in cursive writing (Velmora Gems) but the actual headings and font on the website to be in a widely used font on jewelry websites. Please no hot pink colours or anything neon..
no times new roman font..

```html
<!DOCTYPE html>
<html lang="en">
<head>
<meta charset="utf-8">
<title>Velmora Gems – Custom Diamond Jewellery</title>
<link rel="stylesheet" href="https://fonts.googleapis.com/css2?family=PT+Sans:wght@400;700&family=PT+Sans+Narrow:wght@400;700&family=Oswald:wght@300;400;600&family=Great+Vibes&display=swap">
<style>
  :root{
    --black:#000;
    --ink:#1a1a1a;
    --white:#fff;
    --paper:#f3f3f3;
    --card:#ececec;
    --navy:#0b2a63;
    --navy-line:#1f4a96;
    --dot-blue:#3a7bd5;
    --grey-text:#6b6b6b;
    --title-grey:#4a4a4a;
    --rule:#dcdcdc;
  }
  *{box-sizing:border-box;margin:0;padding:0}
  html,body{width:1200px;height:1158px;overflow:hidden}
  body{position:relative;background:var(--white);font-family:"PT Sans",sans-serif;color:var(--ink)}
  .abs{position:absolute}

  .topbar{left:0;top:0;width:1200px;height:50px;background:var(--black)}
  .search{left:745px;top:13px;width:200px;height:24px;display:flex}
  .search-field{flex:1;background:#2a2a2a;border:1px solid #3a3a3a}
  .search-btn{width:46px;background:#555;color:#eee;font-size:8px;display:flex;align-items:center;justify-content:center;letter-spacing:.3px}
  .login{left:979px;top:16px;color:var(--white);font-size:13px}

  .backdrop{left:0;top:50px;width:1200px;height:818px;background:var(--paper)}

  .brand{left:123px;top:80px;display:flex;align-items:center;gap:8px}
  .brand-dot{width:14px;height:14px;border-radius:50%;background:var(--ink)}
  .brand-name{font-family:"PT Sans",sans-serif;font-size:26px;color:var(--ink)}

  .bag{left:960px;top:90px;width:44px;height:56px;background:linear-gradient(#fafafa,#cfcfcf);border-radius:2px}
  .bag-label{left:892px;top:151px;font-size:12px;color:var(--grey-text);letter-spacing:-.3px}

  .nav{left:120px;top:174px;width:961px;height:53px;background:var(--black)}
  .nav-links{left:23px;top:16px;display:flex;gap:23px;list-style:none}
  .nav-links li{color:var(--white);font-size:18px}
  .quick-contact{left:784px;top:12px;width:150px;height:27px;background:var(--navy);color:var(--white);font-size:14px;font-weight:700;display:flex;align-items:center;padding-left:19px;gap:14px}

  .hero{left:121px;top:232px;width:960px;height:388px;background:var(--black)}
  .hero-photo{left:130px;top:32px;width:260px;height:356px;background:radial-gradient(ellipse at 45% 40%,#e6e6e6 0%,#9a9a9a 40%,#2a2a2a 70%,#000 85%)}
  .hero-title{right:62px;top:78px;font-family:"Oswald",sans-serif;font-weight:600;font-size:50px;color:var(--white);letter-spacing:-.5px;line-height:1}
  .hero-sub{right:61px;top:156px;font-family:"Oswald",sans-serif;font-weight:300;font-size:21px;color:var(--white);line-height:1}
  .hero-cta{left:667px;top:208px;width:232px;height:55px;background:var(--navy);border:1px solid var(--navy-line);color:var(--white);font-size:20px;font-weight:700;display:flex;align-items:center;justify-content:center;letter-spacing:.3px}
  .hero-note{right:61px;top:273px;color:var(--white);font-size:13px}
  .dots{left:442px;top:348px;display:flex;gap:8px}
  .dots span{width:13px;height:13px;border-radius:50%;background:var(--white)}
  .dots span.active{background:var(--dot-blue)}

  .card{top:638px;width:300px;height:189px;background:var(--card)}
  .card-title{left:18px;top:44px;font-size:27px;font-weight:700;color:var(--title-grey);line-height:1}
  .card-sub{left:18px;top:80px;font-family:"PT Sans Narrow",sans-serif;font-size:29px;color:var(--title-grey);line-height:1}
  .buy{left:18px;top:124px;width:84px;height:26px;background:var(--black);color:var(--white);font-size:11px;display:flex;align-items:center;justify-content:center}
  .card-photo{left:150px;top:30px;width:110px;height:118px;background:radial-gradient(ellipse,#fafafa 0%,#c9c9c9 55%,var(--card) 75%)}

  .footer-col{top:888px;list-style:none}
  .footer-col li{font-size:11px;color:var(--grey-text);line-height:23px}
  .social{left:934px;top:888px;width:126px}
  .social-row{position:absolute;left:0;width:126px;display:flex;justify-content:space-between;align-items:center;font-size:11px;color:var(--grey-text)}
  .social-row i{width:27px;height:27px;border-radius:50%;background:var(--black);display:block}

  .promise{top:1040px;font-family:"PT Sans Narrow",sans-serif;font-size:17px;color:var(--ink)}
  .divider{top:1030px;width:1px;height:40px;background:var(--rule)}
  .rule{left:0;top:1089px;width:1200px;height:1px;background:var(--rule)}
  .legal{left:0;top:1113px;width:1200px;text-align:center;font-size:11px;color:var(--grey-text)}
</style>
</head>
<body>
  <div class="abs topbar">
    <div class="abs search"><div class="search-field"></div><div class="search-btn">SEARCH</div></div>
    <div class="abs login">LOGIN</div>
  </div>

  <div class="abs backdrop"></div>

  <div class="abs brand"><span class="brand-dot"></span><span class="brand-name">Velmora Gems</span></div>
  <div class="abs bag" role="img" aria-label="Shopping bag"></div>
  <div class="abs bag-label">Shopping Bag Selected (0)</div>

  <nav class="abs nav">
    <ul class="abs nav-links">
      <li>Home</li><li>About Us</li><li>Custom Jewllery</li><li>Collections</li><li>Contact Us</li>
    </ul>
    <div class="abs quick-contact">Quick Contact
      <svg width="10" height="8" viewBox="0 0 10 8"><path d="M0 0h10L5 8z" fill="#3a7bd5"/></svg>
    </div>
  </nav>

  <section class="abs hero">
    <div class="abs hero-photo" role="img" aria-label="Platinum solitaire diamond engagement ring with reflection"></div>
    <h1 class="abs hero-title">WE DO CUSTOM MADE</h1>
    <p class="abs hero-sub">NECKLACES, EARRINGS, BRACELETS ETC</p>
    <div class="abs hero-cta">CUSTOM JEWELLERY</div>
    <p class="abs hero-note">Create Your Own Jewellery</p>
    <div class="abs dots"><span></span><span></span><span></span><span class="active"></span></div>
  </section>

  <div class="abs card" style="left:128px">
    <div class="abs card-title">Necklace</div><div class="abs card-sub">Collections</div>
    <div class="abs buy">BUY NOW</div>
    <div class="abs card-photo" role="img" aria-label="Diamond necklace"></div>
  </div>
  <div class="abs card" style="left:447px">
    <div class="abs card-title" style="left:16px">Earring</div><div class="abs card-sub" style="left:16px">Collections</div>
    <div class="abs buy">BUY NOW</div>
    <div class="abs card-photo" role="img" aria-label="Pair of diamond flower earrings"></div>
  </div>
  <div class="abs card" style="left:769px">
    <div class="abs card-title" style="left:16px">Bracelet</div><div class="abs card-sub" style="left:16px">Collections</div>
    <div class="abs buy" style="left:17px">BUY NOW</div>
    <div class="abs card-photo" role="img" aria-label="Diamond link bracelet"></div>
  </div>

  <ul class="abs footer-col" style="left:128px;top:883px;line-height:22px">
    <li>Home</li><li>About Us</li><li>Custom Jewllery</li><li>Collections</li><li>Contact Us</li>
  </ul>
  <ul class="abs footer-col" style="left:369px;top:883px">
    <li>Contact Us</li><li>Customer Services</li><li>Terms &amp; Conditions</li><li>Privacy Policy</li>
  </ul>
  <ul class="abs footer-col" style="left:609px;top:883px">
    <li>Delivery &amp; Returns’</li><li>Returns Policy</li><li>Store Locator</li><li>Gift Card</li><li>Custom Jewellery</li>
  </ul>
  <div class="abs social">
    <div class="social-row" style="top:-3px">Friendwall<i></i></div>
    <div class="social-row" style="top:38px">Chirpline<i></i></div>
    <div class="social-row" style="top:84px">Workwise<i></i></div>
  </div>

  <p class="abs promise" style="left:130px">Exquisite craftsmanship a finest quality diamonds</p>
  <div class="abs divider" style="left:423px"></div>
  <p class="abs promise" style="left:440px">Will beat any competitors price by twenty to seventy percent guaranteed</p>
  <div class="abs divider" style="left:867px"></div>
  <p class="abs promise" style="left:890px">Price quotes within 24 hours</p>

  <div class="abs rule"></div>
  <p class="abs legal">©2013 Company Name , All Rights Reserved &nbsp;|&nbsp; Privacy Policy &nbsp; | &nbsp;Terms &amp; Conditions</p>
</body>
</html>
```